Harborline Auto LLC

Car Dealer Customer Service
Address: 2874 Cresthaven Road, Shelbyville, TN 37162
web: www.harborlineautoxq.net
email: harborlineautoxq@mailnest.example
Phone: (931) 555-0148
Phone: (629) 555-0173

```html
<!DOCTYPE html>
<html lang="en">
<head>
<meta charset="utf-8">
<title>Harborline Auto – Business Card</title>
<link href="https://fonts.googleapis.com/css2?family=Poppins:wght@400;500;600;700&display=swap" rel="stylesheet">
<style>
  :root {
    --bg: #2b2b2b;
    --paper: #f3f3f2;
    --blue: #1e74a6;
    --blue-deep: #17679a;
    --gold: #e3a83a;
    --ink: #1d1d1d;
    --white: #ffffff;
    --mist: rgba(30, 116, 166, .07);
  }
  * { margin: 0; padding: 0; box-sizing: border-box; }
  html, body { width: 1200px; height: 1138px; overflow: hidden; }
  body { background: var(--bg); font-family: "Poppins", sans-serif; position: relative; }

  .card {
    position: absolute; left: 274px; width: 622px; height: 375px;
    border-radius: 16px; overflow: hidden; background: var(--paper);
    box-shadow: 0 6px 14px rgba(0,0,0,.35);
  }
  .card--front { top: 186px; }
  .card--back { top: 608px; background: linear-gradient(135deg, var(--blue-deep), var(--blue)); }

  .front__mark {
    position: absolute; left: 330px; top: 30px; width: 270px; height: 270px;
    border-radius: 50%; border: 46px solid var(--mist);
  }

  .brand { position: absolute; display: flex; align-items: center; gap: 12px;
    color: var(--blue); font-weight: 700; white-space: nowrap; letter-spacing: .5px; }
  .brand__dot { width: 16px; height: 16px; border-radius: 50%; background: var(--gold); flex: none; }
  .card--front .brand { left: 50%; top: 212px; transform: translateX(-50%); font-size: 31px; line-height: 1; }

  .front__web { position: absolute; left: 0; right: 0; top: 321px; display: flex;
    justify-content: center; align-items: center; gap: 26px; font-size: 15px; color: var(--ink); line-height: 1; }
  .front__rule { width: 52px; height: 2px; background: var(--gold); }
  .front__band { position: absolute; left: 0; bottom: 0; width: 100%; height: 19px; display: flex; }
  .front__band span { flex: 1; }
  .front__band .band-blue { background: var(--blue); }
  .front__band .band-gold { background: var(--gold); }

  .back__shape { position: absolute; inset: 0; }
  .card--back .brand { left: 348px; top: 190px; font-size: 23px; gap: 9px; line-height: 1; }
  .card--back .brand__dot { width: 12px; height: 12px; }

  .person { position: absolute; left: 28px; top: 40px; }
  .person__name { color: var(--gold); font-weight: 600; font-size: 23px; line-height: 1.2; }
  .person__role { color: var(--white); font-size: 16px; margin-top: 2px; }

  .contact { position: absolute; left: 28px; top: 228px; color: var(--white); font-size: 16px; list-style: none; }
  .contact li { display: flex; align-items: center; gap: 10px; height: 22px; white-space: nowrap; }
  .contact .phone { color: var(--gold); font-weight: 600; letter-spacing: .5px; }
  .contact .gap { margin-top: 5px; }
  .contact .address { margin-top: 5px; }
  .contact svg { width: 14px; height: 14px; flex: none; }
</style>
</head>
<body>

<section class="card card--front">
  <div class="front__mark" aria-hidden="true"></div>
  <div class="brand"><span class="brand__dot"></span>HARBORLINE AUTO</div>
  <div class="front__web"><span class="front__rule"></span>www.harborlineautoxq.net<span class="front__rule"></span></div>
  <div class="front__band"><span class="band-blue"></span><span class="band-gold"></span></div>
</section>

<section class="card card--back">
  <svg class="back__shape" viewBox="0 0 622 375" preserveAspectRatio="none" aria-hidden="true">
    <path fill="#e3a83a" d="M290 0 H622 V284 C520 290 415 292 362 272 C298 250 270 180 270 110 C270 60 280 20 290 0 Z"/>
    <path fill="#f3f3f2" d="M300 0 H622 V280 C520 282 420 282 370 265 C310 245 282 180 280 110 C279 60 290 20 300 0 Z"/>
  </svg>

  <div class="person">
    <div class="person__name">Darren Colwell</div>
    <div class="person__role">Managing Director</div>
  </div>

  <ul class="contact">
    <li class="phone">
      <svg viewBox="0 0 16 16"><path fill="#e3a83a" d="M2 6c0-2 2-3 6-3s6 1 6 3l-3 1-1-2H6L5 7 2 6zm2 2h8l1 6H3l1-6zm4 1.5a2 2 0 100 4 2 2 0 000-4z"/></svg>931-555-0148</li>
    <li class="phone">
      <svg viewBox="0 0 16 16"><path fill="#e3a83a" d="M2 6c0-2 2-3 6-3s6 1 6 3l-3 1-1-2H6L5 7 2 6zm2 2h8l1 6H3l1-6zm4 1.5a2 2 0 100 4 2 2 0 000-4z"/></svg>629-555-0173</li>
    <li class="gap">
      <svg viewBox="0 0 16 16"><path fill="#e3a83a" d="M1 3h14v10H1z"/><path fill="none" stroke="#1e74a6" stroke-width="1.3" d="M1 3l7 6 7-6"/></svg>www.harborlineautoxq.net</li>
    <li>
      <svg viewBox="0 0 16 16"><g fill="none" stroke="#e3a83a" stroke-width="1.4"><circle cx="8" cy="8" r="6.3"/><ellipse cx="8" cy="8" rx="2.6" ry="6.3"/><path d="M1.7 8h12.6"/></g></svg>harborlineautoxq@mailnest.example</li>
    <li class="address">2874 Cresthaven Road, Shelbyville, TN 37162</li>
  </ul>

  <div class="brand"><span class="brand__dot"></span>HARBORLINE AUTO</div>
</section>

</body>
</html>
```